Copper Lantern

Need a business card for our restaurant. Restaurant and Bar in the mountains of North Idaho. Rustic looking card

rustic design, wood and metal looking, primarily neutral colors

• Name, address, phone number, website, email address

```html
<!DOCTYPE html>
<html lang="en">
<head>
<meta charset="utf-8">
<title>Copper Lantern — Business Card</title>
<link rel="stylesheet" href="https://fonts.googleapis.com/css2?family=Lato:wght@400;700&display=swap">
<style>
  :root {
    --backdrop: #e4e4e4;
    --card: #ffffff;
    --ink: #1a1a1a;
    --ink-soft: #333333;
    --rule: #3a3a3a;
    --shadow: rgba(0, 0, 0, 0.18);
  }
  * { box-sizing: border-box; margin: 0; padding: 0; }
  html, body {
    width: 1200px;
    height: 900px;
    overflow: hidden;
    background: var(--backdrop);
    font-family: "Lato", sans-serif;
    color: var(--ink);
  }
  .sheet {
    width: 1200px;
    height: 900px;
    display: flex;
    flex-direction: column;
    align-items: center;
    justify-content: center;
    gap: 40px;
  }
  .card {
    position: relative;
    width: 700px;
    height: 400px;
    background: var(--card);
    border-radius: 28px;
    box-shadow: 0 8px 24px var(--shadow);
  }

  /* Brand name, set in the text face */
  .brand {
    display: flex;
    align-items: center;
    gap: 12px;
    font-weight: 700;
    color: var(--ink);
    letter-spacing: 0.06em;
    text-transform: uppercase;
  }
  .brand-dot {
    flex: none;
    border: 3px solid var(--ink);
    border-radius: 50%;
  }

  /* Front */
  .card-front {
    display: flex;
    align-items: center;
    justify-content: center;
  }
  .card-front .brand { font-size: 34px; }
  .card-front .brand-dot { width: 22px; height: 22px; }

  /* Back */
  .card-back .brand {
    position: absolute;
    top: 92px;
    right: 44px;
    font-size: 22px;
  }
  .card-back .brand-dot { width: 16px; height: 16px; border-width: 2px; }

  .rule-main {
    position: absolute;
    left: 40px;
    right: 40px;
    top: 214px;
    border-top: 1.5px solid var(--rule);
  }
  .person {
    position: absolute;
    left: 40px;
    top: 236px;
  }
  .person-name {
    font-size: 27px;
    font-weight: 700;
    line-height: 1.15;
  }
  .person-role {
    font-size: 18px;
    color: var(--ink-soft);
    margin-top: 6px;
  }
  .rule-short {
    width: 270px;
    border-top: 1.5px solid var(--rule);
    margin-top: 10px;
  }
  .contact-list {
    list-style: none;
    margin-top: 10px;
  }
  .contact-item {
    display: flex;
    align-items: center;
    gap: 12px;
    font-size: 18px;
    line-height: 28px;
    color: var(--ink-soft);
  }
  .contact-icon { width: 16px; height: 16px; flex: none; fill: var(--ink); }

  .address {
    position: absolute;
    right: 44px;
    top: 236px;
    text-align: right;
    font-size: 19px;
    line-height: 1.35;
    color: var(--ink-soft);
    font-style: normal;
  }
</style>
</head>
<body>
<main class="sheet">

  <section class="card card-front" aria-label="Card front">
    <div class="brand"><span class="brand-dot"></span>Copper Lantern</div>
  </section>

  <section class="card card-back" aria-label="Card back">
    <div class="brand"><span class="brand-dot"></span>Copper Lantern</div>

    <div class="rule-main"></div>

    <div class="person">
      <h1 class="person-name">Jonathan Smith</h1>
      <p class="person-role">Owner</p>
      <div class="rule-short"></div>
      <ul class="contact-list">
        <li class="contact-item">
          <svg class="contact-icon" viewBox="0 0 24 24" aria-hidden="true"><path d="M6.6 10.8a15.2 15.2 0 0 0 6.6 6.6l2.2-2.2c.3-.3.7-.4 1-.2 1.1.4 2.3.6 3.6.6.6 0 1 .4 1 1V20c0 .6-.4 1-1 1A17 17 0 0 1 3 4c0-.6.4-1 1-1h3.5c.6 0 1 .4 1 1 0 1.3.2 2.5.6 3.6.1.3 0 .7-.2 1z"/></svg>
          123.456.7890
        </li>
        <li class="contact-item">
          <svg class="contact-icon" viewBox="0 0 24 24" aria-hidden="true"><path d="M2 5h20v14H2z M2 5l10 8 10-8" fill="none" stroke="#1a1a1a" stroke-width="0"/><path d="M2 5h20L12 12.5z"/><path d="M2 7.2l10 7.6 10-7.6V19H2z"/></svg>
          info@webname.com
        </li>
        <li class="contact-item">
          <svg class="contact-icon" viewBox="0 0 24 24" aria-hidden="true"><circle cx="12" cy="12" r="9.5" fill="none" stroke="#1a1a1a" stroke-width="2"/><path d="M8 5c2 2 1 4 3 5s3 0 3 2-3 2-3 5l-1 3c-2-2-2-4-3-5S5 12 5 10s2-3 3-5zM16 6c1 1 3 2 3 5-1 0-2-1-3-1s-1-2 0-4z"/></svg>
          www.website.com
        </li>
      </ul>
    </div>

    <address class="address">
      421, Address line goes here<br>
      45452, Country name
    </address>
  </section>

</main>
</body>
</html>
```